Willow Creek Gatherings Event Planning in need of a design!!

Event Planning company, does a variety of events. I like simple more rustic designs focused on almond blossoms. We are based out of Northern California, the heart of almond country. I would like to see colors in light pinks, beige, light browns, whites or creams. the final design should communicate rustic simplicity. Below are some pictures of Almond blossoms and design ideas I prefer the one called Tulip Grove. Thanks

Target Market(s)

Women in the mid twenties and older. They should be in the upper middle class in need of an amazing party design and coordinator

Industry/Entity Type

Event Planning

Contact Information for Business Card

Maren Lockwood 530-624-0295almondbaffairs@gmail.comalmondblossomaffairs.com

Font styles to use
Other font styles liked:
• Amatic SC

Requirements
Must have
• almond blossom
• my information
• simplicity
Nice to have
• rustic design
• vintage feel
• whimsical
Should not have
• i like pink but not over the top

```html
<!DOCTYPE html>
<html lang="en">
<head>
<meta charset="utf-8">
<title>Willow Creek Gatherings – Business Card</title>
<link rel="stylesheet" href="https://fonts.googleapis.com/css2?family=Arimo:wght@400;700&display=swap">
<style>
  :root {
    --canvas: #d9d9d9;
    --card: #ffffff;
    --mint: #a6d8b3;
    --rose: #c9799f;
    --ink: #2a2a2a;
    --orchard-light: #d9ddd2;
    --orchard-mid: #8ea36c;
    --orchard-deep: #5d7040;
    --blossom-sky: #8fa9cf;
    --blossom-white: #eef0f2;
    --blossom-blur: #a9b394;
    --band: rgba(255,255,255,0.55);
  }
  * { margin: 0; padding: 0; box-sizing: border-box; }
  html, body { width: 1200px; height: 800px; overflow: hidden; }
  body {
    background: var(--canvas);
    font-family: "Arimo", Arial, sans-serif;
    position: relative;
  }
  .card {
    position: absolute;
    left: 290px;
    width: 620px;
    height: 354px;
    background: var(--card);
    overflow: hidden;
    box-shadow: 0 6px 18px rgba(0,0,0,0.25);
  }
  .card--back { top: 24px; }
  .card--front { top: 422px; }

  /* Back side */
  .orchard-photo {
    position: absolute; inset: 0;
    background: linear-gradient(180deg, var(--orchard-light) 0%, var(--orchard-mid) 45%, var(--orchard-deep) 75%, var(--orchard-light) 100%);
  }
  .back-title-band {
    position: absolute; left: 0; right: 0; top: 36px; height: 64px;
    background: var(--band);
    border-top: 2px solid rgba(255,255,255,0.8);
    border-bottom: 2px solid rgba(255,255,255,0.8);
    display: flex; align-items: center; justify-content: center;
  }
  .back-title {
    font-weight: 700; font-size: 24px; letter-spacing: 1px; color: var(--ink);
  }
  .back-web {
    position: absolute; right: 22px; bottom: 18px;
    background: var(--band);
    padding: 4px 10px;
    font-size: 17px; color: var(--ink);
  }

  /* Front side */
  .front-art { position: absolute; inset: 0; }
  .front-company {
    position: absolute; left: 34px; top: 58px;
    font-weight: 700; font-size: 30px; line-height: 1.05;
    color: var(--mint); letter-spacing: 1px;
  }
  .front-contact {
    position: absolute; left: 350px; top: 138px;
    color: var(--mint);
  }
  .contact-name {
    font-weight: 700; font-size: 21px; letter-spacing: 1px; margin-bottom: 8px;
  }
  .contact-line {
    display: flex; align-items: center; gap: 8px;
    font-size: 15px; line-height: 1.4;
  }
  .contact-icon { width: 18px; height: 18px; flex: none; }
</style>
</head>
<body>

<section class="card card--back">
  <div class="orchard-photo" role="img" aria-label="Photo of a blooming almond orchard with a path between rows of trees"></div>
  <div class="back-title-band"><span class="back-title">EVENT PLANNING COMPANY</span></div>
  <div class="back-web">willowcreekgatherings.test</div>
</section>

<section class="card card--front">
  <svg class="front-art" viewBox="0 0 620 354" width="620" height="354">
    <defs>
      <linearGradient id="skyBlossom" x1="0" y1="0" x2="1" y2="1">
        <stop offset="0" stop-color="var(--blossom-sky)"/>
        <stop offset="0.5" stop-color="var(--blossom-white)"/>
        <stop offset="1" stop-color="var(--blossom-sky)"/>
      </linearGradient>
      <linearGradient id="fieldBlossom" x1="0" y1="0" x2="1" y2="1">
        <stop offset="0" stop-color="var(--blossom-white)"/>
        <stop offset="0.5" stop-color="var(--blossom-blur)"/>
        <stop offset="1" stop-color="#c9c2b4"/>
      </linearGradient>
    </defs>
    <path class="rose-band" d="M300 0 C 380 80, 470 128, 620 120 L620 0 Z" fill="var(--rose)"/>
    <path d="M318 0 C 395 68, 480 110, 620 106 L620 0 Z" fill="url(#skyBlossom)" role="img" aria-label="Photo of white almond blossoms against a blue sky"/>
    <path class="rose-band" d="M0 186 C 110 140, 270 130, 340 200 C 370 240, 392 300, 400 354 L0 354 Z" fill="var(--rose)"/>
    <path d="M0 200 C 110 155, 262 146, 328 212 C 356 248, 374 300, 382 354 L0 354 Z" fill="url(#fieldBlossom)" role="img" aria-label="Close-up photo of white almond blossoms on a branch"/>
  </svg>

  <div class="front-company">EVENT PLANNING<br>COMPANY</div>

  <div class="front-contact">
    <div class="contact-name">MAREN LOCKWOOD</div>
    <div class="contact-line">
      <svg class="contact-icon" viewBox="0 0 18 18"><rect width="18" height="18" fill="var(--rose)"/><path d="M5 4 h2 l1 3 -1.5 1 a6 6 0 0 0 3 3 l1-1.5 3 1 v2 a1 1 0 0 1 -1 1 A9 9 0 0 1 4 5 a1 1 0 0 1 1-1z" fill="#fff"/></svg>
      <span>530-817-4362</span>
    </div>
    <div class="contact-line">
      <svg class="contact-icon" viewBox="0 0 18 18"><rect width="18" height="18" fill="var(--rose)"/><rect x="3.5" y="5" width="11" height="8" fill="none" stroke="#fff" stroke-width="1.3"/><path d="M3.5 5 L9 10 L14.5 5" fill="none" stroke="#fff" stroke-width="1.3"/></svg>
      <span>willowcgather@mailbox.test</span>
    </div>
    <div class="contact-line">
      <svg class="contact-icon" viewBox="0 0 18 18"><rect width="18" height="18" fill="var(--rose)"/><circle cx="9" cy="9" r="5.5" fill="none" stroke="#fff" stroke-width="1.2"/><ellipse cx="9" cy="9" rx="2.4" ry="5.5" fill="none" stroke="#fff" stroke-width="1"/><path d="M3.5 9 H14.5" stroke="#fff" stroke-width="1"/></svg>
      <span>willowcreekgatherings.test</span>
    </div>
  </div>
</section>

</body>
</html>
```